PROPERTY MANAGEMENT AND REAL ESTATE

Target Market(s)

real estate owners and investors

Industry/Entity Type

Real Estate

Contact Information for Business Card

BRIGHT LANTERN PROPERTY MANAGEMENT GROUP, LLC
287 North Willowmere Parkway
Suite 240
Hallandale Beach, FL 33071

```html
<!DOCTYPE html>
<html lang="en">
<head>
<meta charset="utf-8">
<title>Bright Lantern Property Management Group – Business Card</title>
<link href="https://fonts.googleapis.com/css2?family=Lato:wght@400;700&display=swap" rel="stylesheet">
<style>
  :root {
    --page: #e9e6e1;
    --card: #ffffff;
    --ink: #0a0a0a;
    --ink-soft: #2a2a2a;
    --crimson: #8e0b12;
    --blush: #c9848b;
    --silver: #c8c8c8;
    --paper-white: #f7f7f7;
  }
  * { margin: 0; padding: 0; box-sizing: border-box; }
  html, body {
    width: 1200px; height: 1020px; overflow: hidden;
    background: var(--page);
    font-family: "Lato", Arial, sans-serif;
  }
  .business-card {
    position: absolute; left: 160px; top: 240px;
    width: 880px; height: 540px;
    background: var(--card);
    box-shadow: 0 18px 40px rgba(0,0,0,0.25);
    overflow: hidden;
  }
  .card-art { position: absolute; inset: 0; }
  .holder { position: absolute; left: 40px; top: 66px; color: #fff; }
  .holder-name { font-weight: 700; font-size: 32px; letter-spacing: 0.5px; line-height: 1.1; }
  .holder-title { font-weight: 400; font-size: 20px; letter-spacing: 0.5px; margin-top: 4px; }
  .brand {
    position: absolute; left: 500px; top: 168px; width: 380px;
    text-align: center; color: var(--ink);
  }
  .brand-mark {
    width: 64px; height: 64px; border-radius: 50%;
    background: var(--crimson); margin: 0 auto 18px;
  }
  .brand-name { font-size: 20px; font-weight: 400; letter-spacing: 1px; line-height: 1.3; }
  .contact-list { position: absolute; left: 20px; top: 350px; list-style: none; }
  .contact-item {
    display: flex; align-items: center; height: 45px;
    font-size: 17px; color: var(--ink-soft);
  }
  .contact-icon {
    width: 38px; height: 18px; background: var(--ink);
    border-bottom: 3px solid var(--crimson);
    display: flex; align-items: center; justify-content: center;
    margin-right: 18px; flex: none;
  }
  .contact-icon svg { width: 11px; height: 11px; fill: #fff; stroke: #fff; }
</style>
</head>
<body>
  <section class="business-card">
    <svg class="card-art" viewBox="0 0 880 540" width="880" height="540" aria-hidden="true">
      <defs>
        <linearGradient id="blush-fade" x1="1" y1="0" x2="0" y2="1">
          <stop offset="0" stop-color="var(--blush)" stop-opacity="1"/>
          <stop offset="1" stop-color="var(--blush)" stop-opacity="0"/>
        </linearGradient>
        <linearGradient id="silver-sweep" x1="0" y1="0" x2="0" y2="1">
          <stop offset="0" stop-color="#f2f2f2"/>
          <stop offset="1" stop-color="var(--silver)"/>
        </linearGradient>
      </defs>
      <path class="blush-band" fill="url(#blush-fade)"
            d="M880,400 C760,430 560,500 380,540 L880,540 Z"/>
      <path class="silver-sweep" fill="url(#silver-sweep)"
            d="M0,246 C60,262 130,276 210,282 C320,290 420,262 520,200 C430,262 330,306 210,310 C130,312 60,300 0,284 Z"/>
      <path class="crimson-line" fill="var(--crimson)"
            d="M880,118 C820,70 760,52 720,58 C650,72 600,120 520,180 C420,250 300,280 200,272 C120,266 50,250 0,236 L0,228 C50,242 120,258 200,264 C300,272 420,242 520,172 C600,112 650,64 720,50 C760,44 820,62 880,112 Z"/>
      <path class="ink-band" fill="var(--ink)"
            d="M0,0 H880 V104 C820,58 760,40 720,46 C650,60 600,108 520,168 C420,238 300,266 200,258 C120,252 50,236 0,222 Z"/>
    </svg>

    <div class="holder">
      <p class="holder-name">DANIEL MARSH</p>
      <p class="holder-title">GENERAL MANAGER</p>
    </div>

    <div class="brand">
      <div class="brand-mark"></div>
      <p class="brand-name">BRIGHT LANTERN PROPERTY<br>MANAGEMENT GROUP, LLC</p>
    </div>

    <ul class="contact-list">
      <li class="contact-item">
        <span class="contact-icon"><svg viewBox="0 0 12 12"><path d="M3 1 L5 3.5 L4 5 C5 7 6 8 7.5 8.5 L9 7.5 L11 9.5 L9.5 11 C5 10.5 1.5 7 1 2.5 Z" stroke="none"/></svg></span>
        012 555 0147
      </li>
      <li class="contact-item">
        <span class="contact-icon"><svg viewBox="0 0 12 12"><rect x="1" y="3" width="10" height="7" fill="none" stroke-width="1.3"/><path d="M1 3 L6 7 L11 3" fill="none" stroke-width="1.3"/></svg></span>
        hello@brightlanternpm.com
      </li>
      <li class="contact-item">
        <span class="contact-icon"><svg viewBox="0 0 12 12"><circle cx="6" cy="6" r="4.8" fill="none" stroke-width="1.2"/><path d="M1.2 6 H10.8 M6 1.2 C3.5 4 3.5 8 6 10.8 M6 1.2 C8.5 4 8.5 8 6 10.8" fill="none" stroke-width="1"/></svg></span>
        www.brightlanternpm.com
      </li>
      <li class="contact-item">
        <span class="contact-icon"><svg viewBox="0 0 12 12"><path d="M6 11.5 C3 7.5 2 6 2 4.5 A4 4 0 0 1 10 4.5 C10 6 9 7.5 6 11.5 Z" stroke="none"/></svg></span>
        287 North Willowmere Parkway, Suite 240
      </li>
    </ul>
  </section>
</body>
</html>
```